Business card for a new innovative and professional lawn care business

We need a business card design for a new lawn care business in Halifax NS Canada. We offer lawn services in Halifax & Bedford. Our services offered include lawn care, garden services, and property maintenance. We take pride in our work and are experienced at what we do. I would like to see a design that is double sided. On the backside I would like the something simple (maybe my logo preferably on blackround (linked below) with website link, Facebook page or something). The front I want to include contact info:
Morgan Pell
phone 902-555-0148
email - brookvaleyards.ca
facebook - Facebook.com/brookvaleyards
Instagram maybe ? - instagram.com/brookvaleyard
Serving Halifax and Bedford for 5 years?
I don't want it to have too much information as I will be passing them out in aim to visit website, or call !
We do want it to include lawn care, garden services and property maintenance.
Basic, catchy, and modern looking !
Logo attached below !

Target Market(s)

Passing business cards to everyone I meet or interact with.

Industry/Entity Type

Lawn Care

Contact Information for Business Card

Double sided with some basic information, with catchy colours and easy to look at.

Font styles to use
Sans Serif

Requirements
Must have
• Must be double sided and have :
• Name, Phone, Email, FB, Website, and 3 main services offered - lawn care, property maintenance, garden services
Nice to have
• Would be nice to have instagram link if it goes well on there
Should not have
• Don't want too much writing or images that are distracting

```html
<!DOCTYPE html>
<html lang="en">
<head>
<meta charset="utf-8">
<title>Brookvale Yards — Business Card</title>
<link rel="stylesheet" href="https://fonts.googleapis.com/css2?family=Montserrat:wght@500;700;800&display=swap">
<style>
  :root {
    --bg: #ece9e3;
    --card: #ffffff;
    --green-dark: #1f7a3a;
    --green-light: #8cc63f;
    --text: #3d4a40;
    --shadow: rgba(0, 0, 0, 0.16);
  }
  * { box-sizing: border-box; margin: 0; padding: 0; }
  html, body { width: 1200px; height: 950px; overflow: hidden; }
  body {
    background: var(--bg);
    font-family: "Montserrat", sans-serif;
    display: flex;
    flex-direction: column;
    align-items: center;
    justify-content: center;
    gap: 50px;
  }
  .card {
    position: relative;
    width: 700px;
    height: 400px;
    background: var(--card);
    box-shadow: 0 10px 30px var(--shadow);
    overflow: hidden;
  }
  .brand {
    display: flex;
    align-items: center;
    gap: 12px;
    color: var(--green-dark);
    font-weight: 800;
  }
  .brand-dot {
    width: 26px; height: 26px;
    border-radius: 50%;
    background: var(--green-dark);
    flex: none;
  }
  .brand-name { display: flex; flex-direction: column; line-height: 1; }
  .brand-name .line1 { font-size: 32px; letter-spacing: 1px; }
  .brand-name .line2 { font-size: 18px; letter-spacing: 10px; margin-top: 6px; }

  /* front side */
  .card--front .brand { position: absolute; left: 40px; top: 215px; }
  .contact {
    position: absolute;
    left: 370px;
    top: 62px;
    color: var(--text);
  }
  .contact-name {
    color: var(--green-dark);
    font-weight: 700;
    font-size: 20px;
    letter-spacing: 3px;
    text-transform: uppercase;
    margin-bottom: 16px;
  }
  .contact-list { list-style: none; }
  .contact-list li {
    display: flex;
    align-items: center;
    gap: 10px;
    font-size: 14px;
    font-weight: 500;
    margin-bottom: 8px;
  }
  .contact-icon { width: 16px; height: 16px; flex: none; }
  .side-band { position: absolute; right: 0; top: 0; width: 180px; height: 400px; }
  .side-url {
    position: absolute;
    right: 22px;
    top: 200px;
    transform: translate(50%, -50%) rotate(-90deg);
    transform-origin: center;
    color: #fff;
    font-size: 13px;
    font-weight: 700;
    letter-spacing: 3px;
    white-space: nowrap;
    text-transform: uppercase;
  }

  /* back side */
  .card--back {
    display: flex;
    flex-direction: column;
    align-items: center;
    justify-content: center;
    gap: 50px;
  }
  .card--back .brand-dot { width: 30px; height: 30px; }
  .card--back .brand-name .line1 { font-size: 40px; }
  .card--back .brand-name .line2 { font-size: 22px; letter-spacing: 12px; }
  .services {
    display: flex;
    gap: 24px;
    list-style: none;
    color: var(--text);
    font-size: 15px;
    font-weight: 500;
  }
  .services li { display: flex; align-items: center; gap: 8px; white-space: nowrap; }
  .tick { width: 14px; height: 14px; flex: none; }
</style>
</head>
<body>

  <section class="card card--front" aria-label="Business card front">
    <div class="brand">
      <span class="brand-dot"></span>
      <span class="brand-name"><span class="line1">BROOKVALE</span><span class="line2">YARDS</span></span>
    </div>

    <div class="contact">
      <p class="contact-name">Morgan Pell</p>
      <ul class="contact-list">
        <li>
          <svg class="contact-icon" viewBox="0 0 16 16"><path fill="#1f7a3a" d="M3 1.5l2.5-.5 1.5 3.5-1.6 1.2a8 8 0 004.4 4.4L11 8.5l3.5 1.5-.5 2.5c-.3 1-1.2 1.6-2.2 1.5C6.5 13.5 2.5 9.5 2 4.2 1.9 3 2.3 2 3 1.5z"/></svg>
          902-555-0148
        </li>
        <li>
          <svg class="contact-icon" viewBox="0 0 16 16"><rect x="1" y="3" width="14" height="10" rx="1.5" fill="#1f7a3a"/><path d="M2 4.5l6 4.5 6-4.5" stroke="#fff" stroke-width="1.3" fill="none"/></svg>
          info@brookvaleyards.ca
        </li>
        <li>
          <svg class="contact-icon" viewBox="0 0 16 16"><rect x="1" y="1" width="14" height="14" rx="2" fill="#1f7a3a"/></svg>
          brookvaleyards
        </li>
        <li>
          <svg class="contact-icon" viewBox="0 0 16 16"><rect x="1" y="1" width="14" height="14" rx="2" fill="#1f7a3a"/></svg>
          brookvaleyard
        </li>
      </ul>
    </div>

    <svg class="side-band" viewBox="0 0 180 400" preserveAspectRatio="none" aria-hidden="true">
      <path d="M150 0 C112 130 100 260 100 400 L180 400 L180 0 Z" fill="#1f7a3a"/>
      <path d="M160 0 C124 130 112 260 112 400 L180 400 L180 0 Z" fill="#8cc63f"/>
    </svg>
    <span class="side-url">www.brookvaleyards.ca</span>
  </section>

  <section class="card card--back" aria-label="Business card back">
    <div class="brand">
      <span class="brand-dot"></span>
      <span class="brand-name"><span class="line1">BROOKVALE</span><span class="line2">YARDS</span></span>
    </div>
    <ul class="services">
      <li>
        <svg class="tick" viewBox="0 0 14 14"><path d="M2 7.5l3 3 7-8" stroke="#8cc63f" stroke-width="2.4" fill="none" stroke-linecap="round"/></svg>
        Lawn Care
      </li>
      <li>
        <svg class="tick" viewBox="0 0 14 14"><path d="M2 7.5l3 3 7-8" stroke="#8cc63f" stroke-width="2.4" fill="none" stroke-linecap="round"/></svg>
        Property Maintenance
      </li>
      <li>
        <svg class="tick" viewBox="0 0 14 14"><path d="M2 7.5l3 3 7-8" stroke="#8cc63f" stroke-width="2.4" fill="none" stroke-linecap="round"/></svg>
        Garden Services
      </li>
    </ul>
  </section>

</body>
</html>
```